Consulting company business cards

We have a base design, but would be willing to update. We have a new logo/"tag" that needs to be added. Current business card design is attached for reference into our "style."

Industry/Entity Type

Business

Contact Information for Business Card

Should contain name and title, office number, mobile number if appropriate, e-mail, website, physical address, and company logo.

Font styles to use
Other font styles liked:
• See current card design on KorvandBCard

Colors
0455a3
85acd3
aaaaaa

Requirements
Must have
• Our colors are navy blue, gray, and a lighter blue
Nice to have
• Design that I can easily drop in new names/titles as we hire employees.

```html
<!DOCTYPE html>
<html lang="en">
<head>
<meta charset="utf-8">
<title>Brannock Business Cards</title>
<link href="https://fonts.googleapis.com/css2?family=Montserrat:wght@400;500;700;800&display=swap" rel="stylesheet">
<style>
  :root {
    --navy: #0b3452;
    --sky: #2aa6e0;
    --logo-blue: #85acd3;
    --gray: #aaaaaa;
    --ink: #1d3b52;
    --rule: #b8c4cf;
    --paper: #ffffff;
    --backdrop: #e9ebee;
  }
  html, body {
    margin: 0;
    padding: 0;
    width: 1200px;
    height: 900px;
    overflow: hidden;
    background: var(--backdrop);
    font-family: "Montserrat", sans-serif;
  }
  .canvas {
    position: relative;
    width: 1200px;
    height: 900px;
  }
  .card {
    position: absolute;
    width: 640px;
    height: 366px;
    border-radius: 26px;
    box-shadow: 0 10px 30px rgba(0,0,0,0.18);
    overflow: hidden;
  }
  /* Back side */
  .card-back {
    left: 90px;
    top: 60px;
    background: var(--navy);
  }
  .mascot-art {
    position: absolute;
    left: 235px;
    top: 70px;
    width: 170px;
    height: 170px;
    border-radius: 46% 54% 40% 60% / 50% 45% 55% 50%;
    background: linear-gradient(160deg, #ffffff, #dfe8ef);
  }
  .back-url {
    position: absolute;
    left: 0;
    right: 0;
    bottom: 44px;
    margin: 0;
    text-align: center;
    color: var(--paper);
    font-size: 19px;
    font-weight: 400;
    letter-spacing: 0.5px;
  }
  .back-url strong { font-weight: 700; }

  /* Front side */
  .card-front {
    left: 470px;
    top: 474px;
    background: var(--paper);
  }
  .brand {
    position: absolute;
    left: 36px;
    top: 152px;
  }
  .brand-line {
    display: flex;
    align-items: center;
    gap: 10px;
  }
  .brand-name {
    font-size: 38px;
    font-weight: 800;
    color: var(--navy);
    letter-spacing: 0.5px;
    line-height: 1;
  }
  .brand-dot {
    width: 30px;
    height: 30px;
    border-radius: 50%;
    background: var(--logo-blue);
  }
  .brand-tag {
    margin-top: 7px;
    font-size: 10.5px;
    font-weight: 500;
    color: var(--gray);
    letter-spacing: 1.5px;
  }
  .divider {
    position: absolute;
    left: 352px;
    top: 60px;
  }
  .contact {
    position: absolute;
    left: 374px;
    top: 62px;
    color: var(--ink);
  }
  .person-name {
    font-size: 21px;
    font-weight: 800;
    color: var(--sky);
    letter-spacing: 0.5px;
    margin: 0;
  }
  .person-title {
    font-size: 13.5px;
    font-weight: 500;
    letter-spacing: 1px;
    margin: 2px 0 16px;
  }
  .address {
    font-size: 14px;
    line-height: 1.3;
    margin: 0 0 14px;
  }
  .contact-list {
    list-style: none;
    margin: 0;
    padding: 0;
    font-size: 14px;
    line-height: 1.35;
  }
  .contact-list li {
    display: flex;
    align-items: center;
    gap: 8px;
  }
  .contact-list svg {
    width: 11px;
    height: 11px;
    flex: none;
  }
  .web-accent { color: var(--sky); font-weight: 700; }
</style>
</head>
<body>
<main class="canvas">

  <section class="card card-back" aria-label="Card back">
    <div class="mascot-art" role="img" aria-label="White dog head illustration"></div>
    <p class="back-url">www.<strong>BRANNOCKTECH</strong>.com</p>
  </section>

  <section class="card card-front" aria-label="Card front">
    <div class="brand">
      <div class="brand-line">
        <span class="brand-name">BRANNOCK</span>
        <span class="brand-dot"></span>
      </div>
      <div class="brand-tag">A CLOUD CONSULTING COMPANY</div>
    </div>

    <svg class="divider" width="4" height="240" viewBox="0 0 4 240" aria-hidden="true">
      <line x1="2" y1="0" x2="2" y2="240" stroke="#b8c4cf" stroke-width="1.5"/>
    </svg>

    <div class="contact">
      <h1 class="person-name">MARLO KORVAND</h1>
      <p class="person-title">OFFICE MANAGER</p>
      <p class="address">1180 w 41st st<br>fairhaven indiana 46011</p>
      <ul class="contact-list">
        <li>
          <svg viewBox="0 0 12 12" aria-hidden="true"><path d="M2.5 1 L4.5 1 L5.3 3.4 L4 4.4 Q5 6.8 7.6 8 L8.6 6.7 L11 7.5 L11 9.5 Q10.5 11 9 11 Q1 10 1 3 Q1 1.5 2.5 1Z" fill="#2aa6e0"/></svg>
          <span class="contact-text">555.014.2910</span>
        </li>
        <li>
          <svg viewBox="0 0 12 12" aria-hidden="true"><rect x="3" y="0.5" width="6" height="11" rx="1.2" fill="#2aa6e0"/><rect x="4" y="2" width="4" height="7" fill="#fff"/></svg>
          <span class="contact-text">555.014.2971</span>
        </li>
        <li>
          <svg viewBox="0 0 12 12" aria-hidden="true"><rect x="0.5" y="2.5" width="11" height="7.5" rx="1" fill="none" stroke="#2aa6e0" stroke-width="1.2"/><path d="M1 3 L6 7 L11 3" fill="none" stroke="#2aa6e0" stroke-width="1.2"/></svg>
          <span class="contact-text">mkorvand@brannocktech.com</span>
        </li>
        <li>
          <svg viewBox="0 0 12 12" aria-hidden="true"><circle cx="6" cy="6" r="5" fill="none" stroke="#2aa6e0" stroke-width="1.2"/><ellipse cx="6" cy="6" rx="2.2" ry="5" fill="none" stroke="#2aa6e0" stroke-width="1"/><line x1="1" y1="6" x2="11" y2="6" stroke="#2aa6e0" stroke-width="1"/></svg>
          <span class="contact-text">www.<span class="web-accent">BRANNOCKTECH</span>.com</span>
        </li>
      </ul>
    </div>
  </section>

</main>
</body>
</html>
```